Website Development for vaultmerrow.com.au

Build a new Wordpress/Responsive website for vaultmerrow.com.au

Target Market(s)

Compliance Managers, Risk Managers, Information Security and Cyber Security Professionals, Chief Data/Digital Officers, Chief Operating/Financial Officers, Business Continuity Professionals, Disaster Recovery Planners, Small Business Owners, Local/Federal Government entities

Industry/Entity Type

Data Service

Coding

Coded - Design and coding required

Number of Pages Required

5+ page

Font styles to use
Sans Serif

Colors

Designer to choose colors to be used in the design.

Requirements
Must have
• 1. Site Structure: Home Page plus the following chapter-pages for a) Services b) About c) Resources d) Blog e) Contact Us
• 2. Prefer site to built on wordpress and we can purchase a theme if needed (we currently use Kelp9 for other sites)
• 3. Blog needs to be wordpress based
• 4. We will host the site ourselves on our own servers
• 5. Responsive Design
Nice to have
• 1. Livechat capability/interface
• 2. Capability for marketing automation integration (such as hubspot, marketo, infusionsoft etc)
• 3. Capability for CRM integration (Salesforce)

```html
<!DOCTYPE html>
<html lang="en">
<head>
<meta charset="utf-8">
<title>Vault Merrow – Data Service</title>
<link href="https://fonts.googleapis.com/css2?family=Roboto:wght@300;400;500;700;900&display=swap" rel="stylesheet">
<style>
:root{
  --blue:#1a6fc4;
  --blue-dark:#0f4f96;
  --navy:#0d2b4e;
  --ink:#333a44;
  --muted:#6b7480;
  --pale:#e9f2fc;
  --line:#d6dde6;
  --white:#ffffff;
  --grey:#c9ccd1;
}
*{box-sizing:border-box;margin:0;padding:0}
html,body{width:1200px;height:4432px;overflow:hidden}
body{font-family:"Roboto",Arial,sans-serif;color:var(--ink);background:var(--white);position:relative}
section,header,footer{position:relative;width:1200px;overflow:hidden}

/* top bar */
.topbar{height:32px;background:var(--white);border-bottom:1px solid var(--line);display:flex;align-items:center;padding:0 140px;font-size:12px;color:var(--muted)}
.topbar .contact{display:flex;gap:28px}
.topbar .contact span{display:flex;align-items:center;gap:6px}
.topbar .follow{margin-left:auto;display:flex;align-items:center;gap:5px}
.topbar .social{width:18px;height:18px;border-radius:2px;display:inline-block}

/* nav */
.masthead{height:80px;display:flex;align-items:center;padding:0 140px;background:var(--white)}
.brand{display:flex;align-items:center;gap:8px;font-size:30px;font-weight:700;color:var(--blue)}
.brand-dot{width:22px;height:22px;border-radius:50%;background:var(--blue)}
.nav{margin-left:auto;display:flex;gap:4px}
.nav a{font-size:11px;font-weight:500;color:var(--ink);text-decoration:none;padding:8px 14px;text-transform:uppercase}
.nav a.active{background:var(--blue);color:var(--white)}

/* hero */
.hero{height:648px}
.hero-photo{position:absolute;inset:0;background:linear-gradient(100deg,#0b1e3a 0%,#1d3f6d 45%,#6d8fb8 75%,#b7c8dc 100%)}
.hero-title{position:absolute;left:140px;top:250px;font-size:48px;font-weight:700;color:var(--white);line-height:1.15}
.btn{display:inline-block;background:var(--blue);color:var(--white);font-size:15px;font-weight:500;padding:12px 22px;border-radius:3px}
.hero .btn{position:absolute;left:140px;top:392px}
.hero-curve{position:absolute;left:0;bottom:0}

/* about */
.about{height:528px}
.about-photo{position:absolute;left:144px;top:0;width:448px;height:448px;background:linear-gradient(160deg,#e6ecf3,#9fb0c4 60%,#3b4c63)}
.about-body{position:absolute;left:636px;top:8px;width:430px}
.about-head{display:flex;align-items:center;gap:10px;font-size:36px;font-weight:700;color:var(--navy);margin-bottom:6px}
.about-head .brand{font-size:26px}
.about-body p{font-size:13px;line-height:1.55;color:var(--muted);margin-bottom:10px}
.about-body p.cta{color:var(--ink);font-weight:700}
.about-body p.cta span{color:var(--blue)}

/* services */
.services{height:584px;background:var(--pale)}
.sec-title{text-align:center;font-size:38px;font-weight:700;color:var(--navy);text-transform:uppercase}
.sec-intro{text-align:center;font-size:12px;color:var(--muted);width:620px;margin:12px auto 0;line-height:1.6}
.services .sec-title{padding-top:72px}
.svc-core{position:absolute;left:506px;top:250px;width:188px;height:188px;border-radius:50%;background:var(--blue);box-shadow:0 0 0 14px rgba(26,111,196,.15)}
.svc{position:absolute;display:flex;align-items:center;gap:18px;font-size:16px;font-weight:700;line-height:1.3}
.svc.left{justify-content:flex-end;text-align:right;right:730px}
.svc.right{left:730px}
.svc .ico{width:92px;height:92px;border-radius:50%;background:var(--white);border:3px solid var(--blue);display:flex;align-items:center;justify-content:center;flex:none}
.svc.hl .label{color:var(--blue)}
.svc.dk .label{color:var(--navy)}

/* audience */
.audience{height:540px;background:var(--white)}
.audience .sec-title{padding-top:100px;font-size:36px}
.aud-row{position:absolute;left:140px;top:292px;width:920px;display:flex;justify-content:space-around}
.aud{width:160px;text-align:center;font-size:14px;color:var(--navy)}
.aud .ring{width:116px;height:116px;border-radius:50%;margin:0 auto 22px;border:2px solid var(--line);background:var(--white);display:flex;align-items:center;justify-content:center;box-shadow:0 4px 14px rgba(0,0,0,.06)}
.aud.active .ring{border:4px solid var(--blue);width:140px;height:140px;margin-top:-12px;margin-bottom:10px}
.aud.active{color:var(--blue);font-weight:700}
.arrow{position:absolute;width:30px;height:30px;border-radius:50%;background:var(--white);border:1px solid var(--line);display:flex;align-items:center;justify-content:center;color:var(--muted);font-size:14px}

/* team */
.team{height:672px;background:linear-gradient(180deg,var(--blue) 0%,var(--blue-dark) 100%)}
.team .sec-title{color:var(--white);padding-top:84px;font-size:38px}
.team .sub{text-align:center;color:#d7e6f7;font-size:16px;margin-top:4px}
.team-row{position:absolute;left:190px;top:192px;width:820px;display:flex;gap:24px}
.member{flex:1;background:var(--white);padding:12px 12px 18px;text-align:center;border-bottom:4px solid var(--navy)}
.member .photo{height:190px;background:linear-gradient(180deg,#eef1f4,#a9b4c1)}
.member h4{font-size:14px;font-weight:700;color:var(--navy);margin-top:14px;text-transform:uppercase}
.member .role{font-size:11px;color:var(--muted);margin-top:2px}
.member .links{display:flex;justify-content:center;gap:8px;margin-top:8px}
.member .links i{width:8px;height:8px;border-radius:50%;background:var(--grey);display:block}
.team .arrow{top:278px;background:rgba(255,255,255,.9);border:none}

/* blog */
.blog{height:600px;background:var(--white)}
.blog .sec-title{padding-top:60px;font-size:36px}
.posts{position:absolute;left:140px;top:180px;width:920px;display:flex;gap:40px}
.post{flex:1;background:var(--white);box-shadow:0 6px 22px rgba(13,43,78,.12);padding:78px 44px 30px;text-align:center;position:relative;border-bottom:5px solid var(--blue)}
.post .date{position:absolute;left:50%;top:-36px;transform:translateX(-50%);width:100px;height:100px;border-radius:50%;background:var(--white);border:4px solid var(--blue);display:flex;flex-direction:column;align-items:center;justify-content:center;color:var(--navy)}
.post .date b{font-size:38px;line-height:1}
.post .date span{font-size:11px}
.post h3{font-size:15px;font-weight:700;color:var(--navy)}
.post p{font-size:12px;color:var(--muted);line-height:1.6;margin-top:12px}
.post a{display:inline-block;margin-top:12px;font-size:12px;color:var(--blue);border-bottom:1px solid var(--blue)}
.view-all{position:absolute;left:528px;top:520px;width:144px;height:40px;border:2px solid var(--blue);color:var(--blue);font-size:14px;display:flex;align-items:center;justify-content:center}

/* get started */
.start{height:580px}
.start-photo{position:absolute;inset:0;background:linear-gradient(160deg,#1d6cc0 0%,#134f93 55%,#0c3566 100%)}
.start .sec-title{position:relative;color:var(--white);padding-top:140px;font-size:36px}
.form{position:absolute;left:320px;top:232px;width:560px;display:grid;grid-template-columns:1fr 1fr;gap:14px 20px}
.field{height:40px;border-bottom:1px solid rgba(255,255,255,.5);color:#dce9f8;font-size:12px;padding-top:12px}
.field.msg{grid-column:2;grid-row:1 / span 3;height:auto;border:1px solid rgba(255,255,255,.35);padding:12px}
.submit{position:absolute;left:530px;top:500px;width:140px;height:42px;background:#9aa3ad;color:var(--white);font-size:16px;display:flex;align-items:center;justify-content:center}
.chat{position:absolute;right:100px;bottom:22px;width:52px;height:52px;border-radius:50%;background:var(--white);display:flex;align-items:center;justify-content:center}

/* footer */
.footer{height:152px;background:var(--white)}
.footer .bar{height:110px;display:flex;align-items:center;padding:0 140px;border-bottom:1px solid var(--line)}
.footer .nav a{font-size:11px}
.footer .legal{display:flex;justify-content:space-between;padding:14px 140px;font-size:11px;color:var(--muted)}
</style>
</head>
<body>

<header class="topbar">
  <div class="contact">
    <span><svg width="12" height="12" viewBox="0 0 24 24"><path d="M6.6 10.8a15 15 0 0 0 6.6 6.6l2.2-2.2a1 1 0 0 1 1-.25 11.4 11.4 0 0 0 3.6.6 1 1 0 0 1 1 1V20a1 1 0 0 1-1 1A17 17 0 0 1 3 4a1 1 0 0 1 1-1h3.5a1 1 0 0 1 1 1 11.4 11.4 0 0 0 .6 3.6 1 1 0 0 1-.25 1z" fill="#1a6fc4"/></svg>1300 555 014</span>
    <span><svg width="12" height="12" viewBox="0 0 24 24"><rect x="2" y="5" width="20" height="14" rx="2" fill="none" stroke="#1a6fc4" stroke-width="2"/><path d="M2 6l10 7 10-7" fill="none" stroke="#1a6fc4" stroke-width="2"/></svg>info@vaultmerrow.com.au</span>
  </div>
  <div class="follow">Follow us
    <i class="social" style="background:#3b5a98"></i><i class="social" style="background:#2ba6e1"></i><i class="social" style="background:#dc4a38"></i><i class="social" style="background:#0e76a8"></i><i class="social" style="background:#c4302b"></i>
  </div>
</header>

<header class="masthead">
  <div class="brand"><span class="brand-dot"></span>Vault Merrow</div>
  <nav class="nav">
    <a class="active">Home</a><a>About</a><a>Services</a><a>Resources</a><a>Blog</a><a>Contact Us</a>
  </nav>
</header>

<section class="hero">
  <div class="hero-photo" role="img" aria-label="Two colleagues reviewing a laptop in a server room"></div>
  <h1 class="hero-title">Because we care,<br>we're security aware</h1>
  <span class="btn">Contact Us Today</span>
  <svg class="hero-curve" width="1200" height="120" viewBox="0 0 1200 120" preserveAspectRatio="none"><path d="M0 40 Q600 150 1200 30 L1200 120 L0 120 Z" fill="#ffffff"/></svg>
</section>

<section class="about">
  <div class="about-photo" role="img" aria-label="Businessman in a suit working on a laptop"></div>
  <div class="about-body">
    <div class="about-head">About <span class="brand"><span class="brand-dot"></span>Vault Merrow</span></div>
    <p>Vault Merrow is a long established firm that helps teams protect critical data with care, clarity and proven recovery plans built for every size of business.</p>
    <p>We review your systems, find the gaps and design a simple path that keeps your records safe, available and compliant every single day.</p>
    <p>Our people work beside yours, so recovery plans are tested, documented and easy to follow when it matters most.</p>
    <p>From cloud backups to ransomware response, we bring one calm team to every stage of your data journey.</p>
    <p class="cta">Get the support you need now. <span>Contact our 24/7 support line to get started.</span></p>
  </div>
</section>

<section class="services">
  <h2 class="sec-title">Services</h2>
  <p class="sec-intro">We help organisations store, manage and recover their data with confidence. Our services cover every layer of protection and continuity.</p>
  <div class="svc-core"></div>
  <div class="svc left hl" style="top:250px"><span class="label">Data Management<br>Platforms</span><span class="ico"><svg width="40" height="40" viewBox="0 0 24 24" fill="none" stroke="#1a6fc4" stroke-width="1.6"><circle cx="12" cy="12" r="3"/><path d="M12 2v4M12 18v4M2 12h4M18 12h4M5 5l3 3M16 16l3 3M19 5l-3 3M8 16l-3 3"/></svg></span></div>
  <div class="svc left dk" style="top:396px"><span class="label">Data Management<br>Services</span><span class="ico"><svg width="40" height="40" viewBox="0 0 24 24" fill="none" stroke="#0d2b4e" stroke-width="1.6"><ellipse cx="12" cy="5" rx="8" ry="3"/><path d="M4 5v14c0 1.7 3.6 3 8 3s8-1.3 8-3V5M4 12c0 1.7 3.6 3 8 3s8-1.3 8-3"/></svg></span></div>
  <div class="svc right dk" style="top:250px"><span class="ico"><svg width="40" height="40" viewBox="0 0 24 24" fill="none" stroke="#0d2b4e" stroke-width="1.6"><rect x="3" y="10" width="5" height="11"/><rect x="10" y="4" width="5" height="17"/><rect x="17" y="13" width="4" height="8"/></svg></span><span class="label">Industry<br>Solutions</span></div>
  <div class="svc right dk" style="top:396px"><span class="ico"><svg width="40" height="40" viewBox="0 0 24 24" fill="none" stroke="#0d2b4e" stroke-width="1.6"><rect x="5" y="11" width="14" height="10" rx="1"/><path d="M8 11V7a4 4 0 0 1 8 0v4"/></svg></span><span class="label">Ransomware<br>Protection</span></div>
</section>

<section class="audience">
  <h2 class="sec-title">To Whom We Serve</h2>
  <p class="sec-intro">We partner with leaders who carry the weight of data risk, giving them tools and advice that make decisions simpler and safer.</p>
  <span class="arrow" style="left:72px;top:330px">&#8249;</span>
  <span class="arrow" style="right:72px;top:330px">&#8250;</span>
  <div class="aud-row">
    <div class="aud"><div class="ring"><svg width="44" height="44" viewBox="0 0 24 24" fill="none" stroke="#6b7480" stroke-width="1.4"><path d="M12 3l10 18H2z"/><path d="M12 10v5M12 17.5v.5"/></svg></div>Risk Managers</div>
    <div class="aud"><div class="ring"><svg width="44" height="44" viewBox="0 0 24 24" fill="none" stroke="#6b7480" stroke-width="1.4"><path d="M12 2l8 3v6c0 5-3.5 9-8 11-4.5-2-8-6-8-11V5z"/><path d="M8.5 12l2.5 2.5 4.5-5"/></svg></div>Information<br>Security</div>
    <div class="aud active"><div class="ring"><svg width="52" height="52" viewBox="0 0 24 24" fill="none" stroke="#1a6fc4" stroke-width="1.4"><rect x="6" y="6" width="12" height="12" rx="1"/><path d="M9 2v4M15 2v4M9 18v4M15 18v4M2 9h4M2 15h4M18 9h4M18 15h4"/></svg></div>Cyber Security<br>Professionals</div>
    <div class="aud"><div class="ring"><svg width="44" height="44" viewBox="0 0 24 24" fill="none" stroke="#6b7480" stroke-width="1.4"><rect x="3" y="4" width="18" height="12" rx="1"/><path d="M8 20h8M12 16v4"/></svg></div>Chief Data<br>Technicians</div>
    <div class="aud"><div class="ring"><svg width="44" height="44" viewBox="0 0 24 24" fill="none" stroke="#6b7480" stroke-width="1.4"><circle cx="12" cy="8" r="4"/><path d="M4 21c0-4.4 3.6-7 8-7s8 2.6 8 7"/></svg></div>Digital Officers</div>
  </div>
</section>

<section class="team">
  <h2 class="sec-title">Our Team</h2>
  <p class="sub">Our Bestest Team Members</p>
  <span class="arrow" style="left:140px">&#8249;</span>
  <span class="arrow" style="right:140px">&#8250;</span>
  <div class="team-row">
    <div class="member"><div class="photo" role="img" aria-label="Portrait of team member"></div><h4>Corin</h4><p class="role">Designation Here</p><div class="links"><i></i><i></i><i></i></div></div>
    <div class="member"><div class="photo" role="img" aria-label="Portrait of team member"></div><h4>Mara Quell</h4><p class="role">Designation Here</p><div class="links"><i></i><i></i><i></i></div></div>
    <div class="member"><div class="photo" role="img" aria-label="Portrait of team member"></div><h4>Tobin Ashe</h4><p class="role">Designation Here</p><div class="links"><i></i><i></i><i></i></div></div>
    <div class="member"><div class="photo" role="img" aria-label="Portrait of team member"></div><h4>Elis Varden</h4><p class="role">Designation Here</p><div class="links"><i></i><i></i><i></i></div></div>
  </div>
</section>

<section class="blog">
  <h2 class="sec-title">Latest Blog Posts</h2>
  <span class="arrow" style="left:72px;top:362px">&#8249;</span>
  <span class="arrow" style="right:72px;top:362px">&#8250;</span>
  <div class="posts">
    <article class="post"><div class="date"><b>12</b><span>Feb 2018</span></div><h3>The point of using Lorem Ipsum</h3><p>Simple steps help small teams keep backups current, tested and ready, so a lost file never turns into a lost week of work.</p><a>Learn More</a></article>
    <article class="post"><div class="date"><b>06</b><span>Feb 2018</span></div><h3>The point of using Lorem Ipsum</h3><p>Ransomware plans work best when every person knows their role, the contacts to call and the order to restore systems.</p><a>Learn More</a></article>
  </div>
  <span class="view-all">View All</span>
</section>

<section class="start">
  <div class="start-photo" role="img" aria-label="Hand touching a glowing digital network interface"></div>
  <h2 class="sec-title">Let's Get Started</h2>
  <div class="form">
    <div class="field">Your Name</div>
    <div class="field msg">Your Message</div>
    <div class="field">Your Email</div>
    <div class="field">Your Phone</div>
  </div>
  <span class="submit">Submit</span>
  <span class="chat"><svg width="28" height="28" viewBox="0 0 24 24"><path d="M4 4h16v12H9l-5 4z" fill="#1a6fc4"/></svg></span>
</section>

<footer class="footer">
  <div class="bar">
    <div class="brand"><span class="brand-dot"></span>Vault Merrow</div>
    <nav class="nav"><a>Home</a><a>About</a><a>Services</a><a>Resources</a><a>Blog</a><a>Contact Us</a></nav>
  </div>
  <div class="legal"><span>Copyright 2018 All Vault Merrow. All Rights Reserved.</span><span>Terms &amp; Conditions | Privacy Policy</span></div>
</footer>

</body>
</html>
```